Brisk Rainshield - Logo and Advert

Help to provide logo and advert.
Advert is to be short and concise to fit in a printed directory posted around homes.
Ideally the same advert to be able to be blown up as a leaflet.
Use of eco friendly type colours, soft greens and blues.
Logo to be subtle but indicative to roofing and facades.
Breakdown of advert as follows;
Company name:
Brisk Rainshield
Sub title:
Roofing & Façades
Services breakdown:
Pitched (Slating & Tiling)
Flat (Single Ply, Liquid & Mineral Felt)
Hard Metal (Zinc Standing Seam)
Leadwork
Roof lights and lanterns
Generic notes:
100% flame free applications available, eliminating all fire risks to your property. (No gas torch’s etc.).
Expert consultation and advice.
Product warranty and/or insurance backed warranty available.
Fully insured contractor.
Contact information:
Phone number to be confirmed
Email and/or website to be confirmed.
Please feel free to try out different colours and fonts other than outlined. I am not limited to those and open to suggestions.
Target Market(s)
Domestic/Private Home Owners/Small Buidlers
Industry/Entity Type
Roofing
Font styles to use
Look and feel
Each slider illustrates characteristics of the customer's brand and the style your logo design should communicate.

```html
<!DOCTYPE html>
<html lang="en">
<head>
<meta charset="utf-8">
<title>Brisk Rainshield – Logo and Advert</title>
<link rel="stylesheet" href="https://fonts.googleapis.com/css2?family=Montserrat:ital,wght@0,500;0,600;0,700;0,800;0,900;1,800;1,900&display=swap">
<style>
  :root {
    --blue: #1b8fd2;
    --blue-deep: #1370b8;
    --green: #a6cd39;
    --green-dark: #7ea227;
    --red: #e8202a;
    --ink: #111;
    --grey: #58595b;
    --white: #fff;
    --sky-top: #c9dcea;
    --sky-bottom: #eef3f6;
  }
  * { margin: 0; padding: 0; box-sizing: border-box; }
  html, body { width: 1200px; height: 798px; overflow: hidden; background: var(--white); }
  body { position: relative; font-family: "Montserrat", Arial, sans-serif; }

  /* Brand lockups on the left */
  .lockup { position: absolute; left: 150px; width: 264px; text-align: center; }
  .lockup--colour { top: 150px; color: var(--blue); }
  .lockup--mono { top: 435px; color: var(--ink); }
  .lockup__dot { width: 108px; height: 108px; border-radius: 50%; margin: 0 auto 22px; background: currentColor; }
  .lockup--mono .lockup__dot { background: var(--grey); }
  .lockup__name { font-weight: 900; line-height: 1; }
  .lockup__name-main { display: block; font-size: 66px; letter-spacing: -1px; }
  .lockup__name-sub { display: block; font-size: 16px; letter-spacing: 7px; margin-top: 10px; }

  /* Advert */
  .advert { position: absolute; left: 522px; top: 69px; width: 514px; height: 666px; overflow: hidden; }
  .advert__bg { position: absolute; inset: 0; }
  .advert__photo-top { position: absolute; left: 0; top: 0; width: 514px; height: 345px;
    background: linear-gradient(180deg, var(--sky-top) 0%, var(--sky-bottom) 70%, #d5dde2 100%); }
  .photo { position: absolute; left: 240px; width: 251px; }
  .photo--roof { top: 394px; height: 101px; background: linear-gradient(180deg, #6e7a82 0%, #8b8f92 50%, #9a6650 100%); }
  .photo--membrane { top: 508px; height: 102px; background: linear-gradient(90deg, #9fb3c2 0%, #e8eef2 30%, #4f86c0 60%, #2f6aa8 100%); }

  .advert__brand { position: absolute; left: 30px; top: 30px; width: 190px; text-align: center; color: var(--blue); }
  .advert__brand .lockup__dot { width: 80px; height: 80px; margin-bottom: 14px; }
  .advert__brand .lockup__name-main { font-size: 44px; }
  .advert__brand .lockup__name-sub { font-size: 11px; letter-spacing: 5px; margin-top: 6px; }

  .headline { position: absolute; left: 28px; top: 204px; font-size: 37px; font-weight: 900; font-style: italic;
    color: var(--green); letter-spacing: -0.5px; white-space: nowrap;
    text-shadow: 1px 1px 0 #fff, 2px 3px 3px rgba(0,0,0,.35); }

  .promise { position: absolute; left: 243px; width: 271px; display: flex; align-items: stretch; }
  .promise__tick { width: 26px; background: var(--blue); display: flex; align-items: center; justify-content: center; border: 1px solid #fff; }
  .promise__text { flex: 1; background: var(--red); color: var(--white); padding: 0 8px 0 12px; display: flex; flex-direction: column; justify-content: center;
    font-size: 7.6px; font-weight: 700; line-height: 1.2; }
  .promise__text em { font-weight: 900; font-style: italic; }
  .promise__text .big { font-size: 17px; font-weight: 900; font-style: italic; }
  .promise__text .mid { font-size: 13px; font-weight: 900; font-style: italic; }
  .promise--1 { top: 255px; height: 26px; }
  .promise--2 { top: 290px; height: 25px; }
  .promise--3 { top: 323px; height: 26px; }
  .promise--4 { top: 357px; height: 25px; }

  .services-title { position: absolute; left: 27px; top: 356px; font-size: 27px; font-weight: 900; font-style: italic; color: var(--white);
    text-shadow: 1px 2px 3px rgba(0,0,0,.35); letter-spacing: -0.5px; }
  .services { position: absolute; left: 25px; top: 398px; list-style: none; }
  .service { position: relative; height: 39px; padding-left: 45px; color: var(--white); display: flex; flex-direction: column; justify-content: center; }
  .service__icon { position: absolute; left: 0; top: 3px; width: 32px; height: 32px; border-radius: 50%; background: var(--green);
    border: 1.5px solid #fff; box-shadow: 1px 2px 3px rgba(0,0,0,.3); }
  .service__name { font-size: 13px; font-weight: 700; letter-spacing: 0.3px; line-height: 1.05; }
  .service__detail { font-size: 9px; font-weight: 600; margin-top: 2px; }

  .contact-phone { position: absolute; left: 20px; top: 618px; display: flex; align-items: center; gap: 5px;
    color: var(--white); font-size: 27px; font-weight: 900; font-style: italic; }
  .contact-lines { position: absolute; left: 252px; top: 620px; color: var(--white); font-size: 9.6px; font-weight: 700; line-height: 1; }
  .contact-line { display: flex; align-items: center; gap: 6px; height: 17px; }
  .contact-line--web { font-size: 11px; font-weight: 800; }
</style>
</head>
<body>

  <div class="lockup lockup--colour">
    <div class="lockup__dot"></div>
    <p class="lockup__name"><span class="lockup__name-main">BRISK</span><span class="lockup__name-sub">RAINSHIELD</span></p>
  </div>

  <div class="lockup lockup--mono">
    <div class="lockup__dot"></div>
    <p class="lockup__name"><span class="lockup__name-main">BRISK</span><span class="lockup__name-sub">RAINSHIELD</span></p>
  </div>

  <section class="advert">
    <div class="advert__photo-top" role="img" aria-label="Photo of a roofer in hard hat and hi-vis jacket crouching on a metal roof against a pale sky"></div>

    <svg class="advert__bg" width="514" height="666" viewBox="0 0 514 666" aria-hidden="true">
      <polygon points="95,338 514,318 514,666 0,666 0,305" fill="var(--green)"/>
      <polygon points="0,305 240,394 240,609 0,609" fill="var(--blue)"/>
      <rect x="240" y="495" width="31" height="13" fill="var(--blue)"/>
    </svg>

    <div class="photo photo--roof" role="img" aria-label="Photo of a brick house with a grey tiled pitched roof"></div>
    <div class="photo photo--membrane" role="img" aria-label="Photo of a rolled waterproof membrane with water droplets"></div>

    <div class="advert__brand">
      <div class="lockup__dot"></div>
      <p class="lockup__name"><span class="lockup__name-main">BRISK</span><span class="lockup__name-sub">RAINSHIELD</span></p>
    </div>

    <h1 class="headline">ROOFING &amp; FACADES</h1>

    <div class="promise promise--1">
      <span class="promise__tick"><svg width="20" height="18" viewBox="0 0 20 18"><path d="M2 9 L8 15 L18 2" fill="none" stroke="var(--green)" stroke-width="3.5"/></svg></span>
      <p class="promise__text"><span><em>100% FLAME FREE APPLICATIONS</em> AVAILABLE,</span><span>ELIMINATING ALL FIRE RISKS TO YOUR PROPERTY</span></p>
    </div>
    <div class="promise promise--2">
      <span class="promise__tick"><svg width="20" height="18" viewBox="0 0 20 18"><path d="M2 9 L8 15 L18 2" fill="none" stroke="var(--green)" stroke-width="3.5"/></svg></span>
      <p class="promise__text"><span><span class="big">EXPERT</span> CONSULTATION &amp; ADVICE</span></p>
    </div>
    <div class="promise promise--3">
      <span class="promise__tick"><svg width="20" height="18" viewBox="0 0 20 18"><path d="M2 9 L8 15 L18 2" fill="none" stroke="var(--green)" stroke-width="3.5"/></svg></span>
      <p class="promise__text"><span><em>PRODUCT WARRANTY</em> AND/OR <em>INSURANCE</em></span><span><em>BACKED WARRANTY</em> AVAILABLE</span></p>
    </div>
    <div class="promise promise--4">
      <span class="promise__tick"><svg width="20" height="18" viewBox="0 0 20 18"><path d="M2 9 L8 15 L18 2" fill="none" stroke="var(--green)" stroke-width="3.5"/></svg></span>
      <p class="promise__text"><span class="mid">FULLY INSURED CONTRACTOR</span></p>
    </div>

    <h2 class="services-title">SERVICES:</h2>
    <ul class="services">
      <li class="service"><span class="service__icon"></span><span class="service__name">PITCHED</span><span class="service__detail">(Slating &amp; Tiling)</span></li>
      <li class="service"><span class="service__icon"></span><span class="service__name">FLAT</span><span class="service__detail">(Single Ply, Liquid &amp; Mineral Felt)</span></li>
      <li class="service"><span class="service__icon"></span><span class="service__name">HARD METAL</span><span class="service__detail">(Zinc Standing Seam)</span></li>
      <li class="service"><span class="service__icon"></span><span class="service__name">LEADWORK</span></li>
      <li class="service"><span class="service__icon"></span><span class="service__name">ROOF LIGHTS AND<br>LANTERNS</span></li>
    </ul>

    <p class="contact-phone">
      <svg width="18" height="18" viewBox="0 0 24 24"><path d="M6.6 10.8a15.1 15.1 0 0 0 6.6 6.6l2.2-2.2a1 1 0 0 1 1-.25 11.4 11.4 0 0 0 3.6.57 1 1 0 0 1 1 1V20a1 1 0 0 1-1 1A17 17 0 0 1 3 4a1 1 0 0 1 1-1h3.5a1 1 0 0 1 1 1c0 1.25.2 2.45.57 3.6a1 1 0 0 1-.25 1z" fill="var(--red)"/></svg>
      800 000 000
    </p>
    <div class="contact-lines">
      <p class="contact-line">
        <svg width="10" height="12" viewBox="0 0 10 12"><path d="M5 11.5S1 7 1 4.5a4 4 0 0 1 8 0C9 7 5 11.5 5 11.5z" fill="none" stroke="var(--red)" stroke-width="1.3"/><circle cx="5" cy="4.5" r="1.3" fill="var(--red)"/></svg>
        LOREM IPSUM DOLOR SIT AMET ADIPISCING
      </p>
      <p class="contact-line contact-line--web">
        <svg width="11" height="11" viewBox="0 0 12 12"><circle cx="6" cy="6" r="5" fill="none" stroke="var(--red)" stroke-width="1.2"/><path d="M1 6h10M6 1v10M2.5 3h7M2.5 9h7" stroke="var(--red)" stroke-width="0.9"/></svg>
        WWW.BRISKRAINSHIELD.COM
      </p>
    </div>
  </section>

</body>
</html>
```